Summit Builders Web Site / Business Cards

Construction Company that specializes in Water and Fire Damage, Residential ReModels, Landscaping and Building ADU (Accessory Dwelling Unit)

Growing and changing families often need additional space, and a remodeling project can often provide that. Adding a new area, or repurposing an existing one can satisfy this requirement.

Other times, homeowners want to update the look in their kitchen or bathroom with more than just a change of cabinetry or vanity doors and drawers. Whatever your needs are, Summit Builders has skilled workers who are bonded and insured, and ready to make your dreams and visions a reality.

Target Market(s)

Home Owners

Industry/Entity Type

Construction Company

Contact Information for Business Card

Center Logo with our information on the corners

Back side to be Logo Only
Contact Info
CSLB License # 2418596
info@summitbuildersca.example
www.summitbuildersca.example

Coding

Coded - Design and coding required

Number of Pages Required

5+ page

Font styles to use
Serif
Sans Serif

Requirements
Must have
• Using our Logo Colors
Home
About Us
Services
Projects / Portfolio
Contact Us
Nice to have
• Colors matching our Logo
Should not have
• Black because it doesnt match our logo

```html
<!DOCTYPE html>
<html lang="en">
<head>
<meta charset="utf-8">
<title>Summit Builders</title>
<link href="https://fonts.googleapis.com/css2?family=Mulish:wght@400;600;700;800;900&display=swap" rel="stylesheet">
<style>
:root{
  --orange:#f26a1b;
  --orange-deep:#e0520f;
  --rust:#8a3a14;
  --brown:#4a2a1c;
  --brown-deep:#3d2318;
  --heading:#3a2e2a;
  --ink:#3f3a38;
  --muted:#6b6b6b;
  --line:#e3e3e3;
  --soft:#f4f4f4;
  --white:#ffffff;
}
*{box-sizing:border-box;margin:0;padding:0}
html,body{width:1200px;height:4264px;overflow:hidden}
body{position:relative;font-family:'Mulish',sans-serif;color:var(--ink);background:var(--white)}
.abs{position:absolute}
.btn{position:absolute;display:flex;align-items:center;justify-content:center;font-size:12px;font-weight:700;border-radius:2px}
.btn-orange{background:var(--orange);color:var(--white)}
.btn-outline{border:1px solid #cfcfcf;color:var(--ink);background:var(--white)}

/* top bar */
.topbar{top:0;left:0;width:1200px;height:45px;background:#f3f3f3}
.topbar span{position:absolute;top:15px;font-size:12px;color:#444}
.nav{top:45px;left:0;width:1200px;height:55px;background:var(--white)}
.brand{position:absolute;display:flex;align-items:center;gap:8px;font-weight:900;color:var(--heading);letter-spacing:1px}
.brand i{display:block;width:18px;height:18px;background:var(--orange)}
.nav a{position:absolute;top:20px;font-size:11px;color:#333;text-decoration:none}
.nav a.active{color:var(--orange)}
.nav a.active:before{content:"";position:absolute;left:0;right:0;top:-20px;height:2px;background:var(--orange)}

/* hero */
.hero{top:100px;left:0;width:1200px;height:502px;
  background:
   radial-gradient(ellipse 260px 300px at 330px 330px,rgba(240,200,60,.35),transparent 70%),
   radial-gradient(ellipse 140px 90px at 300px 80px,rgba(255,170,40,.5),transparent 70%),
   linear-gradient(90deg,#e4571a 0%,#d4481a 25%,#b2401c 45%,#7a3420 65%,#5b2c20 82%,#4e2a22 100%)}
.hero-text{position:absolute;right:114px;top:118px;text-align:right;color:var(--white)}
.hero-text .kicker{font-size:21px;font-weight:600}
.hero-text h1{font-size:72px;line-height:68px;font-weight:900;margin-top:8px}
.hero-text p{font-size:14px;line-height:19px;margin-top:12px}
.social{top:510px;left:1163px;width:37px}
.social div{width:37px;height:35px;margin-bottom:1px}

/* headings */
.sec-title{position:absolute;left:0;width:1200px;text-align:center;font-size:31px;font-weight:800;color:var(--heading)}
.sec-sub{position:absolute;left:0;width:1200px;text-align:center;font-size:13px;color:#333}
.rule{position:absolute;left:575px;width:50px;height:2px;background:#bbb}

/* clients */
.clients-title{top:683px;left:114px;font-size:23px;font-weight:800;color:var(--heading)}
.clients-title em{font-style:normal;color:var(--orange)}
.client{top:741px;width:137px;height:83px;background:var(--white);box-shadow:0 2px 10px rgba(0,0,0,.08);display:flex;align-items:center;justify-content:center;font-size:15px;font-weight:700;color:#8a8a8a;letter-spacing:1px}
.pager{top:688px;left:1047px;width:40px;height:20px;border:1px solid #ddd}

/* services */
.card{top:1084px;width:300px;height:460px;background:var(--white);box-shadow:0 4px 18px rgba(0,0,0,.08);text-align:center}
.card .ph{height:218px}
.card h3{margin-top:42px;font-size:21px;font-weight:700;color:#333}
.card p{margin:30px auto 0;width:230px;font-size:11px;line-height:18px;color:#666}
.card .btn{left:96px;top:399px;width:108px;height:31px}
.arrow{width:18px;height:20px}

/* stats */
.stats{top:1667px;left:0;width:1200px;height:294px;
  background:
   radial-gradient(ellipse 500px 180px at 800px 140px,rgba(190,70,10,.35),transparent 70%),
   linear-gradient(180deg,#f57a22,#f26a1b 45%,#e9640f)}
.stat{position:absolute;top:86px;width:200px;margin-left:-100px;text-align:center;color:var(--white)}
.stat .num{margin-top:12px;font-size:40px;font-weight:900}
.stat .lbl{font-size:12px;font-weight:600;margin-top:2px}

/* who */
.who-copy{top:2143px;left:190px;width:820px;text-align:center;font-size:11.5px;line-height:19px;color:#333}
.point{position:absolute;font-size:12px;font-weight:800;line-height:16px;color:#333}
.dot{position:absolute;width:56px;height:56px;border-radius:50%;background:var(--white);box-shadow:0 3px 12px rgba(0,0,0,.12);display:flex;align-items:center;justify-content:center}
.horizon{top:2435px;left:190px;width:828px;height:3px;background:linear-gradient(90deg,transparent,#6a5a52 50%,transparent)}

/* projects */
.projects{top:2598px;left:0;width:1200px;height:541px;
  background:
   radial-gradient(ellipse 380px 300px at 1050px 150px,rgba(214,100,30,.55),transparent 70%),
   linear-gradient(90deg,#4a2e22 0%,#54301f 45%,#7a3a18 80%,#8e4416 100%)}
.projects h2{position:absolute;left:114px;top:102px;font-size:31px;line-height:34px;font-weight:900;color:var(--white)}
.tile{position:absolute;border:2px solid #efe5de}
.play{position:absolute;width:70px;height:70px;border-radius:50%;background:var(--white);display:flex;align-items:center;justify-content:center}

/* testimonial */
.t-panel{top:3451px;left:0;width:576px;height:227px;background:var(--soft)}
.t-title{top:3247px;left:645px;font-size:31px;line-height:40px;font-weight:900;color:#3a3330}
.t-quote{top:3430px;left:645px;width:440px;font-size:12.5px;line-height:25px;color:#444}
.t-line{top:3553px;left:645px;width:445px;height:1px;background:var(--line)}
.t-name{top:3565px;left:727px;font-size:15px;font-weight:800;color:var(--orange)}
.t-role{top:3584px;left:727px;font-size:13px;color:#444}

/* footer */
.footer{top:3760px;left:0;width:1200px;height:470px;
  background:
   radial-gradient(ellipse 420px 260px at 300px 120px,rgba(140,70,35,.35),transparent 70%),
   radial-gradient(ellipse 420px 260px at 1000px 360px,rgba(150,60,20,.3),transparent 70%),
   linear-gradient(180deg,#4a2c20,#3f251b)}
.fcol{position:absolute;top:85px;color:#e0d2ca}
.fcol h4{font-size:17px;font-weight:800;color:var(--white)}
.fcol h4+.bar{width:36px;height:2px;background:#b08a76;margin:18px 0 14px}
.fcol .link{font-size:11px;line-height:29px}
.fcol b{display:block;color:var(--white);font-size:12px;margin-top:14px}
.fcol .sm{font-size:10.5px;line-height:14px}
.field{position:relative;height:48px;border-bottom:1px solid #7a5e50;font-size:11px;color:#d6c6bd;padding:22px 0 0 30px}
.field:before{content:"";position:absolute;left:4px;top:23px;width:11px;height:11px;border-radius:2px;background:#cbb8ad}
.copy{top:4230px;left:0;width:1200px;height:34px;background:var(--orange);color:var(--white);font-size:12px;font-weight:600;display:flex;align-items:center;justify-content:center}
</style>
</head>
<body>

<!-- top bar -->
<div class="abs topbar">
  <span style="left:522px">ISO 9001:2017</span>
  <span style="left:648px;display:flex;gap:8px;align-items:center;top:13px">
    <svg width="18" height="12" viewBox="0 0 18 12"><rect x="0.5" y="0.5" width="17" height="11" fill="none" stroke="#f26a1b"/><path d="M1 1l8 6 8-6" fill="none" stroke="#f26a1b"/></svg>
    office@summitbuildersca.example</span>
  <span style="left:890px;display:flex;gap:8px;align-items:center;top:12px">
    <svg width="18" height="18" viewBox="0 0 24 24"><path d="M6 3l4 4-2 3c1 2 4 5 6 6l3-2 4 4-3 3C10 21 3 14 3 6z" fill="#f26a1b"/></svg>
    Call Us +1 555 013 2840</span>
</div>

<!-- nav -->
<nav class="abs nav">
  <div class="brand" style="left:119px;top:15px;font-size:20px"><i></i>SUMMIT BUILDERS</div>
  <a class="active" href="#" style="left:384px">Home</a>
  <a href="#" style="left:455px">About Us</a>
  <a href="#" style="left:564px">Services</a>
  <a href="#" style="left:648px">Projects / Portfolio</a>
  <a href="#" style="left:786px">Contact Us</a>
  <div class="btn btn-orange" style="left:903px;top:8px;width:184px;height:36px">Get a Free Quote</div>
</nav>

<!-- hero -->
<section class="abs hero" role="img" aria-label="Construction worker in hard hat and safety vest reviewing building plans on site">
  <div class="hero-text">
    <div class="kicker">The Best Choose Us</div>
    <h1>BECAUSE<br>WE DELIVER</h1>
    <p>We specializes in Water and Fire Damage, Residential<br>ReModels, Landscaping and Building ADU</p>
  </div>
  <div class="btn btn-orange" style="left:902px;top:350px;width:185px;height:42px">Get a Free Quote</div>
</section>
<div class="abs social" aria-label="Social links">
  <div style="background:#3f5fa3"></div>
  <div style="background:#39a9e0"></div>
  <div style="background:#c13584"></div>
</div>

<!-- clients -->
<h2 class="abs clients-title">OUR <em>CLIENTS</em></h2>
<div class="abs pager">
  <svg width="40" height="20" viewBox="0 0 40 20"><path d="M15 10H7m3-3l-3 3 3 3" fill="none" stroke="#999" stroke-width="1.5"/><path d="M25 10h8m-3-3l3 3-3 3" fill="none" stroke="#f26a1b" stroke-width="1.5"/></svg>
</div>
<div class="abs client" style="left:112px">NORTHFRAME</div>
<div class="abs client" style="left:280px">BRIGHTLINE</div>
<div class="abs client" style="left:448px">OAKPOINT</div>
<div class="abs client" style="left:616px">GREYSTONE</div>
<div class="abs client" style="left:784px">FIELDWORK</div>
<div class="abs client" style="left:950px">LUMEN</div>
<div class="abs" style="top:887px;left:112px;width:975px;height:1px;background:var(--line)"></div>

<!-- what we do -->
<h2 class="sec-title" style="top:968px">WHAT WE DO</h2>
<p class="sec-sub" style="top:1013px">We specializes in Water and Fire Damage, Residential ReModels, Landscaping and Building ADU (Accessory Dwelling Unit)</p>
<div class="rule" style="top:1053px"></div>

<svg class="abs arrow" style="left:57px;top:1304px" viewBox="0 0 18 20"><path d="M7 1H1v18h6" fill="none" stroke="#555" stroke-width="1.5"/><path d="M16 10H6m3-3l-3 3 3 3" fill="none" stroke="#555" stroke-width="1.5"/></svg>
<svg class="abs arrow" style="left:1124px;top:1304px" viewBox="0 0 18 20"><path d="M11 1h6v18h-6" fill="none" stroke="#f26a1b" stroke-width="1.5"/><path d="M2 10h10m-3-3l3 3-3 3" fill="none" stroke="#f26a1b" stroke-width="1.5"/></svg>

<article class="abs card" style="left:112px">
  <div class="ph" role="img" aria-label="Builders reviewing plans in front of a new house" style="background:radial-gradient(ellipse 60px 40px at 230px 170px,rgba(245,200,40,.7),transparent 70%),linear-gradient(180deg,#cfd6dd 0%,#d9cbb4 35%,#b59c7c 60%,#8d7f72 100%)"></div>
  <h3>Home Construction</h3>
  <p>Lorem Ipsum is simply dummy the printing and typesetting industry. Lorem Ipsum has been the industry.</p>
  <div class="btn btn-outline">Read More</div>
</article>
<article class="abs card" style="left:450px">
  <div class="ph" role="img" aria-label="Blue two-storey house exterior with lit porch at dusk" style="background:radial-gradient(ellipse 70px 50px at 150px 120px,rgba(240,180,90,.6),transparent 70%),linear-gradient(180deg,#a9bccb 0%,#4d5d72 40%,#3f4e60 65%,#5d7a3c 82%,#486530 100%)"></div>
  <h3>Exterior Design</h3>
  <p>Lorem Ipsum is simply dummy the printing and typesetting industry. Lorem Ipsum has been the industry.</p>
  <div class="btn btn-orange">Read More</div>
</article>
<article class="abs card" style="left:788px">
  <div class="ph" role="img" aria-label="Bright open-plan living room interior" style="background:linear-gradient(180deg,#f1efeb 0%,#d9d6d0 45%,#9e9992 70%,#ecebe8 85%,#7d7873 100%)"></div>
  <h3>Interior Design</h3>
  <p>Lorem Ipsum is simply dummy the printing and typesetting industry. Lorem Ipsum has been the industry.</p>
  <div class="btn btn-outline">Read More</div>
</article>

<!-- stats -->
<section class="abs stats" role="img" aria-label="Orange band with silhouettes of construction crew and project statistics">
  <div class="stat" style="left:233px">
    <svg width="54" height="52" viewBox="0 0 54 52" fill="none" stroke="#fff" stroke-width="2"><rect x="6" y="18" width="16" height="30"/><rect x="26" y="26" width="22" height="22"/><path d="M4 48h46"/></svg>
    <div class="num">53</div><div class="lbl">TOTAL PROJECTS</div></div>
  <div class="stat" style="left:467px">
    <svg width="54" height="52" viewBox="0 0 54 52" fill="none" stroke="#fff" stroke-width="2"><path d="M16 20a11 11 0 0122 0z"/><circle cx="27" cy="28" r="7"/><path d="M12 50c2-9 8-13 15-13s13 4 15 13"/></svg>
    <div class="num">371</div><div class="lbl">STAFF MEMBERS</div></div>
  <div class="stat" style="left:710px">
    <svg width="54" height="52" viewBox="0 0 54 52" fill="none" stroke="#fff" stroke-width="2"><path d="M6 22l14 4 12-6 16 8-4 16-14 2-12-6-10 2z"/><circle cx="24" cy="12" r="6"/></svg>
    <div class="num">15</div><div class="lbl">WORKING IN STATES</div></div>
  <div class="stat" style="left:963px">
    <svg width="54" height="52" viewBox="0 0 54 52" fill="none" stroke="#fff" stroke-width="2"><circle cx="24" cy="24" r="18"/><path d="M24 12v12l8 6"/><circle cx="40" cy="38" r="8"/></svg>
    <div class="num">2,600</div><div class="lbl">HOURS FOR WORK</div></div>
</section>

<!-- who we are -->
<h2 class="sec-title" style="top:2034px">WHO WE ARE</h2>
<p class="sec-sub" style="top:2079px">We Deliver Landmark Projects</p>
<p class="abs who-copy">We are rethoric question ran over her cheek When she reached the first hills of the Italic Mountains, she had a last view back on the skyline of her hometown Bookmarksgrove, the headline of Alphabet Village and the subline of her own road, the Line Lane.</p>

<svg class="abs" style="top:2220px;left:0" width="1200" height="220" viewBox="0 0 1200 220" fill="none" stroke="#999" stroke-dasharray="4 4">
  <path d="M508 36h40l28 40"/><path d="M690 36h-40l-28 40"/>
  <path d="M468 147h50l20-56"/><path d="M732 147h-50l-20-56"/>
</svg>
<div class="point" style="left:300px;top:2240px;width:120px;text-align:right">WE'VE REPUTION<br>FOR EXCELLENCE</div>
<div class="dot" style="left:452px;top:2228px"><svg width="24" height="24" viewBox="0 0 24 24" fill="none" stroke="#f26a1b" stroke-width="2"><circle cx="12" cy="10" r="7"/><path d="M8 16l-2 7 6-3 6 3-2-7"/></svg></div>
<div class="point" style="left:781px;top:2240px">GUIDED BY<br>COMMITMENT</div>
<div class="dot" style="left:690px;top:2228px"><svg width="22" height="24" viewBox="0 0 22 24" fill="none" stroke="#f26a1b" stroke-width="2"><rect x="3" y="2" width="16" height="20"/><path d="M7 8h8M7 12h8M7 16h5"/></svg></div>
<div class="point" style="left:260px;top:2351px;width:120px;text-align:right">WE BUILD<br>PARTNERSHIPS</div>
<div class="dot" style="left:412px;top:2339px"><svg width="24" height="24" viewBox="0 0 24 24" fill="none" stroke="#f26a1b" stroke-width="2"><path d="M5 12l5 5 9-10"/></svg></div>
<div class="point" style="left:819px;top:2351px">A TEAM OF<br>PROFESSIONALS</div>
<div class="dot" style="left:732px;top:2339px"><svg width="26" height="22" viewBox="0 0 26 22" fill="none" stroke="#f26a1b" stroke-width="2"><circle cx="8" cy="7" r="4"/><circle cx="18" cy="7" r="4"/><path d="M1 21c1-5 4-7 7-7s6 2 7 7M11 21c1-5 4-7 7-7s6 2 7 7"/></svg></div>

<div class="abs" style="left:555px;top:2330px;width:90px;height:90px;background:var(--orange)"></div>
<div class="abs horizon"></div>
<div class="abs" style="top:2452px;left:0;width:1200px;text-align:center;font-size:40px;font-weight:900;letter-spacing:3px;color:var(--heading)">SUMMIT BUILDERS</div>

<!-- recent projects -->
<section class="abs projects" role="img" aria-label="Dimmed photo of a construction site with warm orange light">
  <h2>RECENT<br>PROJECTS</h2>
  <div class="btn btn-orange" style="left:114px;top:209px;width:111px;height:31px">View All</div>
  <div class="tile" role="img" aria-label="Two-storey house with lit windows at dusk" style="left:359px;top:90px;width:235px;height:178px;background:radial-gradient(ellipse 60px 30px at 120px 120px,rgba(250,200,110,.7),transparent 70%),linear-gradient(180deg,#6f86a8 0%,#9aa6b8 35%,#7d7570 60%,#5c5a58 100%)"></div>
  <div class="tile" role="img" aria-label="School building exterior" style="left:112px;top:280px;width:237px;height:177px;background:linear-gradient(120deg,#e7dcc4 0%,#d6c8a8 40%,#5d86a8 60%,#9fbbd0 80%,#7c8a70 100%)"></div>
  <div class="tile" role="img" aria-label="Brick family house with garage" style="left:359px;top:280px;width:235px;height:177px;background:linear-gradient(180deg,#b9cde0 0%,#d8d6d0 30%,#9a5a44 55%,#7d6a5c 75%,#5c7a3e 100%)"></div>
  <div class="tile" role="img" aria-label="Video of engineers in hard hats on a construction site" style="left:606px;top:90px;width:480px;height:367px;background:radial-gradient(ellipse 160px 100px at 200px 320px,rgba(220,200,90,.35),transparent 70%),linear-gradient(135deg,#54606a 0%,#5e5550 45%,#9a5224 80%,#b86424 100%)">
    <div class="play" style="left:205px;top:148px"><svg width="22" height="24" viewBox="0 0 22 24"><path d="M3 2l17 10L3 22z" fill="none" stroke="#f26a1b" stroke-width="2"/></svg></div>
  </div>
</section>

<!-- testimonial -->
<div class="abs t-panel"></div>
<div class="abs" role="img" aria-label="Video portrait of a smiling client" style="top:3241px;left:114px;width:394px;height:369px;background:radial-gradient(ellipse 120px 150px at 200px 200px,#8a7a72,transparent 75%),linear-gradient(180deg,#8b8790,#5e5a60)">
  <div class="play" style="left:162px;top:150px"><svg width="22" height="24" viewBox="0 0 22 24"><path d="M3 2l17 10L3 22z" fill="none" stroke="#777" stroke-width="2"/></svg></div>
</div>
<h2 class="abs t-title">WHAT PEOPLE ARE<br>SAYING ABOUT SUMMIT<br>BUILDERS</h2>
<svg class="abs" style="top:3432px;left:645px" width="34" height="24" viewBox="0 0 34 24" fill="#ddd"><path d="M0 24V12C0 5 4 1 12 0v5c-4 1-6 3-6 7h6v12zM18 24V12c0-7 4-11 12-12v5c-4 1-6 3-6 7h6v12z"/></svg>
<p class="abs t-quote"><span style="padding-left:52px"></span>SummitBuilders is one of the best general contractors we've worked with. The entire team tactfully delivered a project of exceptional quality while staying on schedule and under budget. We hope to work with Summit again in the near future!"</p>
<div class="abs t-line"></div>
<svg class="abs" style="top:3553px;left:690px" width="30" height="20" viewBox="0 0 30 20"><path d="M0 0l20 18L30 0" fill="#fff" stroke="#e3e3e3"/></svg>
<div class="abs t-name">LAURA BENNETT</div>
<div class="abs t-role">Project Manager</div>
<div class="btn btn-orange" style="left:645px;top:3641px;width:202px;height:37px">View All Client Testimonials</div>

<!-- footer -->
<footer class="abs footer" role="img" aria-label="Dimmed photo of building framework in warm brown tones">
  <div class="fcol" style="left:45px">
    <h4>QUICK INFO</h4><div class="bar"></div>
    <div class="link">Home</div><div class="link">About Us</div><div class="link">Services</div><div class="link">Projects / Portfolio</div><div class="link">Contact Us</div>
  </div>
  <div class="fcol" style="left:237px">
    <h4>CONTACT US</h4><div class="bar"></div>
    <b style="margin-top:0">Address</b>
    <div class="sm">418 W Orchard Ave Fairview,<br>CA 90000</div>
    <b>Daniel R Avery</b>
    <div class="sm">Branch Manager</div>
    <div class="sm" style="margin-top:4px">Office : 555-013-2840<br>Direct : 555-017-6621</div>
    <b style="margin-top:24px">E-mail</b>
    <div class="sm">info@summitbuildersca.example</div>
  </div>
  <div class="fcol" style="left:482px;width:290px">
    <h4>WORKING HOURS</h4><div class="bar"></div>
    <div class="sm" style="line-height:17px">we work 7 days a week, every day excluding major holidays. contact us if you have an emergency, with our hotline and contact form.</div>
    <div class="sm" style="margin-top:20px;line-height:25px;display:grid;grid-template-columns:148px 1fr">
      <span>Monday – Friday</span><span>10:00 – 16:00</span>
      <span>Saturday:</span><span>12:00 – 15:00</span>
      <span>Sunday And Holidays:</span><span>09:00 – 12:00</span>
    </div>
  </div>
  <div class="fcol" style="left:839px;top:80px;width:308px">
    <h4>LET'S DISCUSS WHAT'S NEXT</h4>
    <div class="sm" style="margin-top:8px">Have a project or a Question? We'd Love to hear from you.</div>
    <div class="field">Name</div>
    <div class="field">Email</div>
    <div class="field">Phone</div>
    <div class="field" style="height:74px">Message</div>
    <div class="btn btn-orange" style="position:relative;margin-top:22px;width:116px;height:32px">Submit Now</div>
  </div>
</footer>
<div class="abs copy">Copyright © 2020 SUMMIT BUILDERS &nbsp;|&nbsp; All Right Reserved</div>

</body>
</html>
```